IT’S NOT A CLEANING, IT’S YOUR LIFE! TOP TEN REASONS WHY THIS IS NOT JUST A “CLEANING”

We made a list for our patients to let them know why our hygiene appointments are different than other cleanings. Since this is a lot of information, we would like it easily readable within 4-5 feet but we do not want the post to be HUGE. Please see below:

IT’S NOT A CLEANING, IT’S YOUR LIFE!
TOP TEN REASONS WHY THIS IS NOT JUST A “CLEANING”

10. We make you look better. Healthy teeth and gums are more attractive. Recent studies
show that the smile is the first thing people notice and that people with better looking teeth
are more confident and successful.

9. We can relieve your headaches. During your hygiene visit we evaluate for serious bite
issues, many of which lead to muscle soreness, headaches, and migraines.

8. We check for oral cancer. Oral cancer kills 1 person per hour 24 hours a day. The death rate for oral cancer is higher than cancers we routinely hear about such as cervical, thyroid and skin cancer.

7. We make you smell better. During your hygiene visit we eliminate many of the germs that live under your gum tissue and cause bad breath.

6. We save you money. By utilizing the latest dental technology (digital x-rays, mouth
cameras, and magnification glasses) we can help with early detection of tooth and gum
problems and save you the cost of gum surgery, root canals, and implants.

5. We clean in places you cannot. We clean under the gum line and between teeth where
most of the germs hide and cause dental disease. 40% of the bacteria in your mouth lives in
between your teeth.

4. We prevent pain. We identify tooth decay that can lead to nerve involvement and pain,
root canal, and tooth loss.

3. We save your teeth. Most tooth loss is from periodontal/gum disease. At each visit we
evaluate the health of your gums and bone with our periodontal screening. Periodontal
disease, like high blood pressure, is symptomless until it is in advanced stages.

2. We protect your loved ones. Studies have proven that the bacteria that cause dental
disease can be transmitted from person to person. Think about that the next time you kiss
someone!

1. We prolong life. Researchers have linked the inflammation and infection found in the
mouth to heart attacks, strokes, and Alzheimer’s. By reducing infection in your mouth we can
greatly improve your overall health!

```html
<!DOCTYPE html>
<html lang="en">
<head>
<meta charset="utf-8">
<title>It's Not a Cleaning, It's Your Life! – Top Ten Reasons</title>
<link rel="stylesheet" href="https://fonts.googleapis.com/css2?family=Oswald:wght@700&family=Roboto+Condensed:wght@400&display=swap">
<style>
  :root {
    --page-bg: #ececec;
    --paper: #ffffff;
    --headline-blue: #1a8fd6;
    --headline-green: #8cc63f;
    --wave-light-green: #cde59a;
    --wave-green: #9acd3c;
    --panel-blue-top: #55b6ea;
    --panel-blue-bottom: #1496d8;
    --list-text: #ffffff;
    --badge-bg: #0d4f8a;
    --photo-light: #e9dfd6;
    --photo-mid: #cfa58f;
    --photo-dark: #4a3328;
  }
  * { margin: 0; padding: 0; box-sizing: border-box; }
  html, body {
    width: 890px; height: 1200px; overflow: hidden;
    background: var(--page-bg);
  }
  .poster {
    position: absolute; left: 78px; top: 33px;
    width: 734px; height: 1133px;
    background: var(--paper);
    overflow: hidden;
  }
  .portrait {
    position: absolute; left: 0; top: 0;
    width: 430px; height: 520px;
    background: radial-gradient(ellipse at 38% 40%, var(--photo-mid) 0%, var(--photo-light) 45%, var(--paper) 75%),
                linear-gradient(90deg, var(--photo-dark) 0%, transparent 30%);
  }
  .headline {
    position: absolute; left: 309px; top: 20px; width: 420px;
    font-family: "Oswald", sans-serif; font-weight: 700;
    font-size: 56px; line-height: 0.94; letter-spacing: -1px;
    text-transform: uppercase; color: var(--headline-blue);
  }
  .headline .accent { color: var(--headline-green); display: block; }
  .waves { position: absolute; left: 0; top: 455px; width: 734px; height: 678px; }
  .reasons {
    position: absolute; left: 80px; top: 612px; width: 575px;
    list-style: none;
    font-family: "Roboto Condensed", sans-serif; font-size: 11px; line-height: 1.3;
    color: var(--list-text);
  }
  .reasons li { position: relative; padding-left: 24px; margin-bottom: 14px; }
  .reasons .badge {
    position: absolute; left: 0; top: 0;
    width: 14px; height: 14px; border-radius: 50%;
    background: var(--badge-bg); color: var(--list-text);
    font-size: 8px; font-weight: 700; line-height: 14px; text-align: center;
  }
</style>
</head>
<body>
  <main class="poster">
    <div class="portrait" role="img" aria-label="Photo of a young woman with her finger on her chin, looking up thoughtfully"></div>

    <h1 class="headline">
      It’s not a cleaning,<br>it’s your life!
      <span class="accent">Top ten reasons</span>
      Why this is<br>not just a<br>“cleaning”
    </h1>

    <svg class="waves" viewBox="0 0 734 678" preserveAspectRatio="none" aria-hidden="true">
      <defs>
        <linearGradient id="panelBlue" x1="0" y1="0" x2="0" y2="1">
          <stop offset="0" stop-color="var(--panel-blue-top)"/>
          <stop offset="1" stop-color="var(--panel-blue-bottom)"/>
        </linearGradient>
      </defs>
      <path d="M0 10 C180 0 380 60 734 60 L734 678 L0 678 Z" fill="var(--wave-light-green)"/>
      <path d="M0 35 C200 20 420 80 734 95 L734 678 L0 678 Z" fill="var(--wave-green)"/>
      <path d="M0 100 C200 45 480 50 734 120 L734 678 L0 678 Z" fill="url(#panelBlue)"/>
    </svg>

    <ol class="reasons">
      <li><span class="badge">10</span>We make you look better. Healthy teeth and gums are more attractive. Recent studies show that the smile is the first thing people notice and that people with better looking teeth are more confident and successful.</li>
      <li><span class="badge">9</span>We can relieve your headaches. During your hygiene visit we evaluate for serious bite issues, many of which lead to muscle soreness, headaches, and migraines.</li>
      <li><span class="badge">8</span>We check for oral cancer. Oral cancer kills 1 person per hour 24 hours a day. The death rate for oral cancer is higher than cancers we routinely hear about such as cervical, thyroid and skin cancer.</li>
      <li><span class="badge">7</span>We make you smell better. During your hygiene visit we eliminate many of the germs that live under your gum tissue and cause bad breath.</li>
      <li><span class="badge">6</span>We save you money. By utilizing the latest dental technology (digital x-rays, mouth cameras, and magnification glasses) we can help with early detection of tooth and gum problems and save you the cost of gum surgery, root canals, and implants.</li>
      <li><span class="badge">5</span>We clean in places you cannot. We clean under the gum line and between teeth where most of the germs hide and cause dental disease. 40% of the bacteria in your mouth lives in between your teeth.</li>
      <li><span class="badge">4</span>We prevent pain. We identify tooth decay that can lead to nerve involvement and pain, root canal, and tooth loss.</li>
      <li><span class="badge">3</span>We save your teeth. Most tooth loss is from periodontal/gum disease. At each visit we evaluate the health of your gums and bone with our periodontal screening. Periodontal disease, like high blood pressure, is symptomless until it is in advanced stages.</li>
      <li><span class="badge">2</span>We protect your loved ones. Studies have proven that the bacteria that cause dental disease can be transmitted from person to person. Think about that the next time you kiss someone!</li>
      <li><span class="badge">1</span>We prolong life. Researchers have linked the inflammation and infection found in the mouth to heart attacks, strokes, and Alzheimer’s. By reducing infection in your mouth we can greatly improve your overall health!</li>
    </ol>
  </main>
</body>
</html>
```